Executive Business Card for Healthcare Company [Need Today]

I need a business card design for a healthcare company. The only branding the company has thus far is a logo. The cards will be utilized by company executives. The design I envision will be vibrant and appealing but with a corporate feel. They shouldn't be too casual or playful. I would like to complete this project TODAY if possible.

Target Market(s)

Healthcare vendors, other executives in healthcare and pharmaceuticals

Industry/Entity Type

Pharmaceutical

Contact Information for Business Card

See attachment

Font styles to use
Serif
Sans Serif

Colors

Designer to choose colors to be used in the design.

```html
<!DOCTYPE html>
<html lang="en">
<head>
<meta charset="utf-8">
<title>Corvela Therapeutics – Business Card</title>
<link href="https://fonts.googleapis.com/css2?family=Arimo:wght@400;700&display=swap" rel="stylesheet">
<style>
  :root {
    --backdrop: #3a3a3a;
    --card-light: #ededed;
    --teal: #3bbfc7;
    --green: #6cc49a;
    --ink: #2b2b2b;
    --rule: #9a9a9a;
    --white: #ffffff;
  }
  * { box-sizing: border-box; margin: 0; padding: 0; }
  html, body { width: 1200px; height: 900px; overflow: hidden; }
  body {
    position: relative;
    background: var(--backdrop);
    font-family: "Arimo", Arial, sans-serif;
    color: var(--ink);
  }
  .card {
    position: absolute;
    top: 170px;
    width: 347px;
    height: 561px;
  }
  .card-front { left: 259px; background: var(--card-light); }
  .card-back {
    left: 631px;
    background: linear-gradient(to bottom, var(--teal) 0%, var(--teal) 50%, var(--green) 50%, var(--green) 100%);
  }

  .brand {
    position: absolute;
    top: 113px;
    left: 31px;
    display: flex;
    align-items: center;
    gap: 12px;
  }
  .brand-mark {
    width: 86px; height: 86px;
    border: 3px solid var(--green);
    border-radius: 50%;
    flex: none;
  }
  .brand-divider { width: 1px; height: 44px; background: var(--rule); }
  .brand-name {
    font-size: 22px;
    line-height: 1.15;
    font-weight: 400;
    color: var(--teal);
  }

  .contact {
    position: absolute;
    top: 310px;
    left: 0; right: 0;
    text-align: center;
    font-size: 16px;
    line-height: 20px;
  }
  .person-name {
    font-size: 20px;
    font-weight: 700;
    line-height: 24px;
    letter-spacing: 0.3px;
  }
  .person-name .first { color: var(--teal); }
  .person-name .last { color: var(--green); }
  .person-title { margin-top: 1px; }

  .icon-rule {
    display: flex;
    align-items: center;
    justify-content: center;
    gap: 3px;
    margin: 9px 70px 5px;
  }
  .icon-rule .line { flex: 1; height: 1px; background: var(--rule); }
  .icon-rule svg { width: 16px; height: 16px; display: block; }
  .plain-rule { height: 1px; background: var(--rule); margin: 10px 70px 13px; }

  .company-name {
    color: var(--green);
    font-weight: 700;
    letter-spacing: 0.3px;
  }

  .back-emblem {
    position: absolute;
    left: 1px; top: 108px;
    width: 344px; height: 344px;
    border-radius: 50%;
    background: var(--green);
    border: 10px solid var(--white);
    display: flex;
    align-items: center;
    justify-content: center;
  }
  .back-emblem span {
    color: var(--white);
    font-size: 30px;
    font-weight: 400;
    text-align: center;
    line-height: 1.2;
  }
</style>
</head>
<body>
  <section class="card card-front">
    <div class="brand">
      <div class="brand-mark"></div>
      <div class="brand-divider"></div>
      <div class="brand-name">Corvela<br>Therapeutics</div>
    </div>

    <div class="contact">
      <p class="person-name"><span class="first">DANIEL</span> <span class="last">MARSH</span></p>
      <p class="person-title">Senior Director of Marketing</p>

      <div class="icon-rule">
        <span class="line"></span>
        <svg viewBox="0 0 16 16" aria-label="Phone">
          <circle cx="8" cy="8" r="7.3" fill="none" stroke="var(--teal)" stroke-width="1"/>
          <path d="M4.5 7.5 Q8 4.8 11.5 7.5 L10.6 8.6 L9.4 7.9 L9.2 7 H6.8 L6.6 7.9 L5.4 8.6 Z M5.5 10 H10.5 L9.6 8.6 H6.4 Z" fill="var(--teal)"/>
        </svg>
        <svg viewBox="0 0 16 16" aria-label="Mobile">
          <circle cx="8" cy="8" r="7.3" fill="none" stroke="var(--teal)" stroke-width="1"/>
          <rect x="5.8" y="4" width="4.4" height="8" rx="0.8" fill="none" stroke="var(--teal)" stroke-width="1"/>
        </svg>
        <svg viewBox="0 0 16 16" aria-label="Email">
          <circle cx="8" cy="8" r="7.3" fill="none" stroke="var(--teal)" stroke-width="1"/>
          <rect x="4.6" y="5.5" width="6.8" height="5" fill="var(--teal)"/>
          <path d="M4.6 5.5 L8 8.4 L11.4 5.5" fill="none" stroke="var(--white)" stroke-width="0.8"/>
        </svg>
        <span class="line"></span>
      </div>

      <p>555-210-4837</p>
      <p>555-368-1925</p>
      <p>dmarsh@corvelarx.com</p>

      <div class="plain-rule"></div>

      <p class="company-name">CORVELA THERAPEUTICS, LLC</p>
      <p>118 N Laurel Street</p>
      <p>Millbrook, GA 30512</p>
    </div>
  </section>

  <section class="card card-back">
    <div class="back-emblem"><span>Corvela<br>Therapeutics</span></div>
  </section>
</body>
</html>
```